Kor'v Meridell Travel

We need a sleek, professional, inviting card to elicit global travel for the experienced and professional traveler. Royal blue, black and silver. (perhaps the wording could be silver with black shadow?-get creative) Maybe a watermark on the front and the full raised logo on the back.
We want a stylish and modern card, but professional.

```html
<!DOCTYPE html>
<html lang="en">
<head>
<meta charset="utf-8">
<title>Kor'v Meridell Travel — Business Card</title>
<link rel="stylesheet" href="https://fonts.googleapis.com/css2?family=Montserrat:wght@600;700&family=Open+Sans:ital,wght@0,400;0,600;1,400&display=swap">
<style>
  :root {
    --stage: #2a2a2a;
    --card: #1c1c1d;
    --edge-blue: #1ea3e6;
    --brand-blue: #23a8e8;
    --brand-green: #8cc63f;
    --silver: #b9b9bc;
    --text-light: #d6d6d8;
    --text-muted: #a4a4a8;
  }
  * { box-sizing: border-box; margin: 0; padding: 0; }
  html, body {
    width: 1200px; height: 900px; overflow: hidden;
    background: var(--stage);
  }
  .canvas {
    position: relative; width: 1200px; height: 900px;
    display: flex; flex-direction: column; align-items: center; justify-content: center;
    gap: 50px;
  }
  .card {
    position: relative; width: 560px; height: 320px;
    background: var(--card);
    border-bottom: 7px solid var(--edge-blue);
    box-shadow: 0 18px 40px rgba(0,0,0,.55);
    overflow: hidden;
  }

  /* Front */
  .front-brand {
    position: absolute; left: 34px; top: 108px; width: 230px;
    display: flex; align-items: center; gap: 10px;
  }
  .brand-dot {
    flex: none; width: 14px; height: 14px; border-radius: 50%;
    background: var(--brand-green);
  }
  .brand-name {
    font-family: "Montserrat", sans-serif; font-weight: 700;
    font-size: 22px; line-height: 1.15; letter-spacing: .5px;
    text-transform: uppercase; color: var(--brand-blue);
  }
  .divider {
    position: absolute; left: 290px; top: 58px; width: 1px; height: 196px;
    background: var(--brand-blue);
  }
  .contact {
    position: absolute; left: 312px; top: 64px;
    font-family: "Open Sans", sans-serif; color: var(--text-light);
  }
  .contact-name {
    font-family: "Montserrat", sans-serif; font-weight: 700;
    font-size: 19px; color: var(--brand-blue); text-transform: uppercase;
    letter-spacing: .3px;
  }
  .contact-role { font-size: 14px; color: var(--text-muted); margin-bottom: 10px; }
  .contact-address { font-size: 14px; line-height: 1.4; margin-bottom: 10px; }
  .contact-list { list-style: none; font-size: 14px; line-height: 1.55; }
  .contact-list li { display: flex; align-items: center; gap: 8px; }
  .contact-list svg { flex: none; width: 12px; height: 12px; fill: var(--brand-green); }

  /* Back */
  .back-brand {
    position: absolute; inset: 0 0 7px 0;
    display: flex; align-items: center; justify-content: center; gap: 16px;
  }
  .back-brand .brand-dot { width: 20px; height: 20px; background: var(--silver); }
  .back-brand .brand-name {
    font-size: 34px; color: var(--silver); text-align: left;
  }
</style>
</head>
<body>
<main class="canvas">

  <section class="card card-front" aria-label="Card front">
    <div class="front-brand">
      <span class="brand-dot"></span>
      <span class="brand-name">Kor'v Meridell Travel</span>
    </div>
    <div class="divider"></div>
    <div class="contact">
      <p class="contact-name">Daren Holloway</p>
      <p class="contact-role">President</p>
      <p class="contact-address">18420 Harbor Crest Way<br>Sea Cove CA 92650</p>
      <ul class="contact-list">
        <li>
          <svg viewBox="0 0 24 24" aria-hidden="true"><path d="M6.6 10.8a15.1 15.1 0 0 0 6.6 6.6l2.2-2.2a1 1 0 0 1 1-.25 11.4 11.4 0 0 0 3.6.57 1 1 0 0 1 1 1V20a1 1 0 0 1-1 1A17 17 0 0 1 3 4a1 1 0 0 1 1-1h3.5a1 1 0 0 1 1 1c0 1.25.2 2.45.57 3.57a1 1 0 0 1-.25 1z"/></svg>
          555-318-2740
        </li>
        <li>
          <svg viewBox="0 0 24 24" aria-hidden="true"><path d="M2 5h20v14H2z M2 5l10 8 10-8" /></svg>
          info@korvmeridell.com
        </li>
        <li>
          <svg viewBox="0 0 24 24" aria-hidden="true"><circle cx="12" cy="12" r="10"/></svg>
          www.korvmeridell.com
        </li>
      </ul>
    </div>
  </section>

  <section class="card card-back" aria-label="Card back">
    <div class="back-brand">
      <span class="brand-dot"></span>
      <span class="brand-name">Kor'v Meridell<br>Travel</span>
    </div>
  </section>

</main>
</body>
</html>
```